indépendant en tant que Massothérapeute et Préparateur Mental, j'ai besoin de ...

Massothérapeute et préparateur mental indépendant, je recherche une carte de visite sobre et dynamique, sans images liées au massage ou à la préparation mentale mais intégrant mon logo. Les couleurs que j'aime bien sont : Blanc, gris, anthracite, noir et jaune

Contact Information for Business Card

carte de préférence Horizontale
neutre qui puisse toucher le deux domaines Massothérapie et préparation mentale

Requirements
Must have
• mon projet doit intégrer au recto:
LOGO
Loïc Bardèze
078 513 26 48
info@loicbardeze.ch
et éventuellement www.loicbardeze.ch

et au verso les deux adresses:

Chemin des Ormilles 7B
1400 Yverdon-les-Bains

Route de la Gravière 9
1700 Fribourg

Should not have
• mon projet ne doit pas contenir d'image en liens avec le massage ni la préparation mentale.

```html
<!DOCTYPE html>
<html lang="fr">
<head>
<meta charset="utf-8">
<title>Loïc Bardèze – Cartes de visite</title>
<link href="https://fonts.googleapis.com/css2?family=Montserrat:wght@300;400;500;800&family=Questrial&display=swap" rel="stylesheet">
<style>
  :root {
    --white: #ffffff;
    --paper: #f4f4f4;
    --light-grey: #e3e3e3;
    --grey: #8a8a8a;
    --anthracite: #2b2b2b;
    --black: #141414;
    --yellow: #f2c91c;
    --yellow-deep: #e2b514;
    --backdrop: #d9d6d0;
  }
  * { box-sizing: border-box; margin: 0; padding: 0; }
  html, body { width: 1200px; height: 780px; overflow: hidden; }
  body {
    background: var(--backdrop);
    font-family: "Questrial", "Century Gothic", sans-serif;
    position: relative;
  }
  .card {
    position: absolute;
    top: 231px;
    width: 540px;
    height: 318px;
    background: var(--paper);
    overflow: hidden;
    box-shadow: 0 10px 26px rgba(0,0,0,.22);
  }
  .card--front { left: 40px; }
  .card--back { left: 620px; background: linear-gradient(135deg, var(--white), var(--light-grey)); }

  /* wordmark */
  .wordmark { position: absolute; display: flex; flex-direction: column; }
  .wordmark__name {
    font-family: "Montserrat", sans-serif;
    font-weight: 800;
    color: var(--black);
    letter-spacing: .5px;
    line-height: 1;
  }
  .wordmark__role {
    font-family: "Montserrat", sans-serif;
    font-weight: 500;
    color: var(--anthracite);
    text-transform: uppercase;
    letter-spacing: .6px;
    margin-top: 5px;
  }
  .card--front .wordmark { left: 34px; top: 40px; }
  .card--front .wordmark__name { font-size: 30px; }
  .card--front .wordmark__role { font-size: 8.5px; }

  /* front blocks */
  .contact-block {
    position: absolute; left: 0; top: 166px; width: 250px; height: 101px;
    background: var(--black);
    padding: 12px 0 0 34px;
  }
  .contact-block__name { color: var(--yellow); font-size: 21px; margin-bottom: 6px; }
  .contact-line {
    display: flex; align-items: center; gap: 8px;
    color: var(--white); font-size: 11.5px; line-height: 19px;
  }
  .contact-line .accent { color: var(--yellow); }
  .contact-icon { width: 14px; height: 14px; flex: none; }

  .address-block {
    position: absolute; left: 250px; top: 88px; width: 225px; height: 179px;
    background: linear-gradient(160deg, var(--yellow), var(--yellow-deep));
    padding: 30px 0 0 22px;
  }
  .address { display: flex; gap: 8px; color: var(--black); font-size: 12.5px; line-height: 17px; margin-bottom: 14px; }
  .address svg { width: 11px; height: 14px; margin-top: 2px; flex: none; }

  .side-strip { position: absolute; left: 475px; top: 88px; width: 65px; height: 179px; background: var(--light-grey); }

  .services-band {
    position: absolute; left: 0; bottom: 0; width: 100%; height: 51px;
    background: linear-gradient(90deg, var(--yellow-deep), var(--yellow));
    display: flex; align-items: center; padding-left: 250px;
    border-top: 6px solid var(--light-grey);
  }
  .services-band p { color: var(--black); font-size: 12.5px; letter-spacing: .2px; }

  /* back */
  .card--back .wordmark { left: 92px; top: 110px; }
  .card--back .wordmark__name { font-size: 38px; }
  .card--back .wordmark__role { font-size: 10.5px; }
  .back-web {
    position: absolute; left: 92px; top: 206px;
    font-family: "Montserrat", sans-serif; font-weight: 400;
    font-size: 13px; letter-spacing: 2.5px; color: var(--grey);
  }
  .back-web .accent { color: var(--yellow-deep); }
  .edge-bar { position: absolute; height: 16px; }
  .edge-bar--top-yellow { left: 150px; top: 0; width: 60px; background: var(--yellow); }
  .edge-bar--top-black { left: 205px; top: 0; width: 335px; background: var(--black); }
  .edge-bar--bottom-black { left: 0; bottom: 0; width: 390px; background: var(--black); }
  .edge-bar--bottom-yellow { left: 390px; bottom: 0; width: 150px; height: 38px; background: var(--yellow); }
</style>
</head>
<body>

<section class="card card--front" aria-label="Recto">
  <div class="wordmark">
    <span class="wordmark__name">Loïc BARDÈZE</span>
    <span class="wordmark__role">Massothérapeute / Préparateur mental</span>
  </div>

  <div class="address-block">
    <div class="address">
      <svg viewBox="0 0 12 16"><path d="M6 0a5 5 0 0 0-5 5c0 4 5 11 5 11s5-7 5-11a5 5 0 0 0-5-5zm0 7a2 2 0 1 1 0-4 2 2 0 0 1 0 4z" fill="#141414"/></svg>
      <p>Chemin des Ormilles 7B<br>1400 Yverdon-les-Bains</p>
    </div>
    <div class="address">
      <svg viewBox="0 0 12 16"><path d="M6 0a5 5 0 0 0-5 5c0 4 5 11 5 11s5-7 5-11a5 5 0 0 0-5-5zm0 7a2 2 0 1 1 0-4 2 2 0 0 1 0 4z" fill="#141414"/></svg>
      <p>Route de la Gravière 9<br>1700 Freiburg</p>
    </div>
  </div>
  <div class="side-strip"></div>

  <div class="contact-block">
    <p class="contact-block__name">Loïc Bardèze</p>
    <p class="contact-line">
      <svg class="contact-icon" viewBox="0 0 14 14"><circle cx="7" cy="7" r="7" fill="#f2c91c"/><path d="M4.6 3.6l1.3 1.6-.7.8c.5 1 1.3 1.8 2.3 2.3l.8-.7 1.6 1.3-.8 1.3C6.6 10 4 7.4 3.8 4.4z" fill="#141414"/></svg>
      078 513 26 48
    </p>
    <p class="contact-line">
      <svg class="contact-icon" viewBox="0 0 14 14"><circle cx="7" cy="7" r="7" fill="#f2c91c"/><rect x="3.5" y="4.5" width="7" height="5" fill="none" stroke="#141414" stroke-width="1"/><path d="M3.5 4.5L7 7.3l3.5-2.8" fill="none" stroke="#141414" stroke-width="1"/></svg>
      info@loicbardeze.ch
    </p>
    <p class="contact-line">
      <svg class="contact-icon" viewBox="0 0 14 14"><circle cx="7" cy="7" r="7" fill="#f2c91c"/><circle cx="7" cy="7" r="3.6" fill="none" stroke="#141414" stroke-width=".9"/><path d="M3.4 7h7.2M7 3.4c-1.6 2-1.6 5.2 0 7.2M7 3.4c1.6 2 1.6 5.2 0 7.2" fill="none" stroke="#141414" stroke-width=".8"/></svg>
      <span>www.<span class="accent">loicbardeze</span>.ch</span>
    </p>
  </div>

  <div class="services-band">
    <p>Sports massage - Therapeutic massage - Relaxing massage</p>
  </div>
</section>

<section class="card card--back" aria-label="Verso">
  <div class="edge-bar edge-bar--top-yellow"></div>
  <div class="edge-bar edge-bar--top-black"></div>
  <div class="wordmark">
    <span class="wordmark__name">Loïc BARDÈZE</span>
    <span class="wordmark__role">Massothérapeute / Préparateur mental</span>
  </div>
  <p class="back-web">www.<span class="accent">loicbardeze</span>.ch</p>
  <div class="edge-bar edge-bar--bottom-black"></div>
  <div class="edge-bar edge-bar--bottom-yellow"></div>
</section>

</body>
</html>
```